Natural Australian skin care company packaging for new product Bath salts

We are moving to fully refillable packaging and need someone to design our refill pouches. we have a number of products we need to do this for but our first one is our natural bath salts. This comes in a 200g tin in a pouch then the pouch can be bought to refill the tin. We can either print on the pouch or do sickers. The tin is a simple matt black tin with white text on the lid. the pouch comes in a gold colour. pictures are in the drop box lid.
Luxury bath salts Pouch - the dimensions are 60*55*180mm, , we can either print directly or do a sticker, We also need the sleeve to go around the tin. The dimensions of the tin are 65x65x70mm. The same text needs to go onto the sleeve as the pouch. The tin is black with white printing on the top (see picture).
Text is as follows
MB logo Calm reed drift 100% pure magnesium bath salts
A rich fragrance of Australian wild flowers (using natural essential oils) with frangipani and gardenia. Sink into the natural ancient salt lake sourced 100% pure magnesium to replenish your skin. Transdermal absorption of magnesium is effective and contributes to electrolyte balance, normal muscle function and aids calcium absorption. The ultimate mineral reset.
Directions: Fill bath, once full put two heaped tablespoons of the salts into the bath (approx 50g). Climb in and relax.
Menzo Balm full logo
Country of Origin: Australia
PO Box 318
Ellory Bay 4612
QLD Australia
www.menzobalm-example.com
ingredients:
magnesium chloride *, parfum **
*naturally sourced from ancient salt lakes
**a combination of essential oils and natural isolates.
e: 200g / 7.05 Oz
We also need the recycle, plastic free, not tested on animal eco friendly symbols.
Please use this link to our press assets and tin and pouch photos.
https://www.filecrate-example.com/sh/kq8vt341plmwx27/BBtoLw__qRsYYjmK-HuvgNeTa?dl=0

```html
<!DOCTYPE html>
<html lang="en">
<head>
<meta charset="utf-8">
<title>Menzo Balm – Magnesium Bath Salts Label</title>
<link rel="stylesheet" href="https://fonts.googleapis.com/css2?family=Arvo:wght@400&family=Kaushan+Script&family=Montserrat:wght@400;500&display=swap">
<style>
  :root {
    --ink: #0b0b0b;
    --paper: #ffffff;
    --backdrop: #e4e4e4;
  }
  * { box-sizing: border-box; margin: 0; padding: 0; }
  html, body {
    width: 1200px;
    height: 991px;
    overflow: hidden;
    background: var(--backdrop);
  }
  .label {
    position: absolute;
    left: 281px;
    top: 45px;
    width: 637px;
    height: 900px;
    overflow: hidden;
    background: var(--paper);
    color: var(--ink);
    font-family: "Montserrat", sans-serif;
  }
  .band { position: absolute; left: 0; width: 100%; display: block; }
  .band--top { top: 0; height: 64px; }
  .band--middle { top: 308px; height: 352px; }
  .band--bottom { top: 838px; height: 62px; }

  .brand {
    position: absolute;
    top: 98px;
    left: 0;
    width: 100%;
    text-align: center;
    font-family: "Montserrat", sans-serif;
    font-weight: 500;
    font-size: 42px;
    letter-spacing: 2px;
    line-height: 1;
  }
  .tagline {
    position: absolute;
    top: 156px;
    left: 0;
    width: 100%;
    text-align: center;
    font-family: "Arvo", serif;
    font-size: 17px;
    letter-spacing: 1.4px;
  }
  .rule {
    position: absolute;
    top: 184px;
    left: 205px;
    width: 227px;
    height: 3px;
    background: var(--ink);
  }
  .product-name {
    position: absolute;
    top: 200px;
    left: 0;
    width: 100%;
    text-align: center;
    font-family: "Kaushan Script", cursive;
    font-size: 26px;
    line-height: 32px;
  }
  .description {
    position: absolute;
    top: 380px;
    left: 49px;
    width: 540px;
    color: var(--paper);
    font-size: 19.4px;
    line-height: 27px;
    text-align: justify;
    text-align-last: center;
  }
  .ingredient {
    position: absolute;
    top: 673px;
    left: 48px;
    display: flex;
    align-items: center;
    gap: 13px;
  }
  .ingredient__mark {
    width: 56px;
    height: 56px;
    border: 3px solid var(--ink);
    border-radius: 50%;
  }
  .ingredient__name { font-size: 14px; line-height: 18px; }
  .features {
    position: absolute;
    top: 742px;
    left: 52px;
    list-style: none;
    font-size: 14px;
    line-height: 18px;
  }
  .features li {
    position: relative;
    padding-left: 18px;
    margin-bottom: 12px;
  }
  .features li::before {
    content: "";
    position: absolute;
    left: 0;
    top: 5px;
    width: 8px;
    height: 8px;
    border-radius: 50%;
    background: var(--ink);
  }
  .eco-icons {
    position: absolute;
    top: 670px;
    left: 437px;
    width: 176px;
    height: 160px;
  }
  .eco-icon { position: absolute; width: 76px; height: 76px; }
  .eco-icon--recycle { left: 0; top: 0; }
  .eco-icon--plastic-free { left: 100px; top: 0; }
  .eco-icon--eco { left: 0; top: 84px; }
  .eco-icon--cruelty-free { left: 100px; top: 84px; }
  .weight {
    position: absolute;
    top: 862px;
    left: 0;
    width: 100%;
    text-align: center;
    color: var(--paper);
    font-size: 19px;
  }
</style>
</head>
<body>
  <main class="label">
    <svg class="band band--top" viewBox="0 0 637 64" preserveAspectRatio="none" aria-hidden="true">
      <path d="M0 0H637V48C560 54 470 46 380 56C290 64 200 50 110 58C60 62 25 54 0 58Z" fill="var(--ink)"/>
    </svg>

    <h1 class="brand">MENZO BALM</h1>
    <p class="tagline">AUSTRALIAN BUSH MEDICINES</p>
    <div class="rule"></div>
    <p class="product-name">100% pure<br>magnesium bath salts</p>

    <svg class="band band--middle" viewBox="0 0 637 352" preserveAspectRatio="none" aria-hidden="true">
      <path d="M0 30C80 22 110 8 190 6C260 0 340 4 420 10C500 16 560 48 637 52V312C560 318 480 330 400 322C300 314 220 336 120 332C70 330 30 326 0 330Z" fill="var(--ink)"/>
    </svg>
    <p class="description">A rich fragrance of Australian wild flowers (using natural essential oils) with frangipani and gardenia. Sink into the natural ancient salt lake sourced 100% pure magnesium to replenish your skin. Transdermal absorption of magnesium is effective and contributes to electrolyte balance, normal muscle function and aids calcium absorption. The ultimate mineral reset.</p>

    <div class="ingredient">
      <span class="ingredient__mark" role="img" aria-label="Magnesium element badge"></span>
      <span class="ingredient__name">MAGNESIUM<br>CHLORIDE</span>
    </div>
    <ul class="features">
      <li>NATURALLY SOURCED FROM<br>ANCIENT SALT LAKES</li>
      <li>A COMBINATION OF ESSENTIAL<br>OILS AND NATURAL ISOLATE</li>
    </ul>

    <div class="eco-icons">
      <svg class="eco-icon eco-icon--recycle" viewBox="0 0 76 76" role="img" aria-label="Recyclable symbol">
        <g fill="var(--ink)">
          <path d="M30 10H46L54 24L60 20L58 38L42 34L48 30L40 17L32 30L22 24Z"/>
          <path d="M8 52L16 38L10 34L27 30L32 46L25 44L20 54H36V64H14C8 64 4 58 8 52Z"/>
          <path d="M42 54H58L50 40L58 36L68 54C71 60 67 64 62 64H48V70L36 59L48 48Z"/>
        </g>
      </svg>
      <svg class="eco-icon eco-icon--plastic-free" viewBox="0 0 76 76" role="img" aria-label="Plastic free badge">
        <circle cx="38" cy="38" r="34" fill="var(--ink)"/>
      </svg>
      <svg class="eco-icon eco-icon--eco" viewBox="0 0 76 76" role="img" aria-label="Eco friendly leaf cycle symbol">
        <circle cx="38" cy="38" r="30" fill="var(--ink)"/>
      </svg>
      <svg class="eco-icon eco-icon--cruelty-free" viewBox="0 0 76 76" role="img" aria-label="Not tested on animals symbol">
        <rect x="8" y="14" width="60" height="48" rx="6" fill="var(--ink)"/>
      </svg>
    </div>

    <svg class="band band--bottom" viewBox="0 0 637 62" preserveAspectRatio="none" aria-hidden="true">
      <path d="M0 20C60 14 110 18 160 10C260 2 360 8 460 4C540 2 600 10 637 14V62H0Z" fill="var(--ink)"/>
    </svg>
    <p class="weight">200g / 7.05 Oz</p>
  </main>
</body>
</html>
```